Veltrix Saves Doctor! HTML BillBoard

I need a HTMl Page that is going to be emailed to Dr's, its about our service and they can push a button if they would like our salesmen to come see them,
The HTML Page should be designed to scare the Dr. so that they want to use our service right away! Use or logo colors plus others you like, this should read like a flyer, and know that doctors will only view for a few seconds before they decide. his project is going to be a 81/2 by 11 inch HTML Flyer that will be Emailed to Doctors
The Main Message is "Veltrix Protects Doctor"
then this:
Lets say Your Worst Case Scenario Happens… Your Patient Dies..... Now the Family Says..... "you got them addicted" and Sues the Practice!
Then This:
What's in Your Chart Right Now That is Protecting You?
Use the catch phrases I have supplied, these work the best for pain drs. please be creative with this project and have fun with it, I will work closely with you and will aide in your design, I have done a lot of projects with pixel harbor, so I am very familiar

Target Market(s)

Pain Management Doctors

Industry/Entity Type

Health Care

Coding

Coded - Design and coding required

Number of Pages Required

1 page

Font styles to use
Sans Serif

Colors
f37122
f8ba93
f78f20
faa54b
fac994

Requirements
Must have
• Must USE exact words I give you on the Document "Veltrix Protects Doctor" t, must look like a Flyer for our service,
• his project is going to be a 81/2 by 11 inch HTML Flyer that will be Emailed to Doctors
• The Main Message is "Veltrix Protects Doctor"
• then this:
• Lets say Your Worst Case Scenario Happens… Your Patient Dies..... Now the Family Says..... "you got them addicted" and Sues the Practice!
• Then This:
• What's in Your Chart Right Now That is Protecting You
Nice to have
• get creative, you can use other pictures along the same idea, chocolate browns and tans, aluminum grey for colors
Should not have
• any changes in our tag lines we provided you

```html
<!DOCTYPE html>
<html lang="en">
<head>
<meta charset="utf-8">
<title>Veltrix Protects Doctor</title>
<link rel="stylesheet" href="https://fonts.googleapis.com/css2?family=Lato:wght@300;400;700&family=Ubuntu:wght@500;700&display=swap">
<style>
  :root {
    --orange: #f37122;
    --orange-deep: #e8501c;
    --brown: #8a3a14;
    --ink: #2b2b2b;
    --soft: #f7f7f7;
    --frame: #e2e2e2;
    --footer: #0d0d0d;
  }
  * { box-sizing: border-box; margin: 0; padding: 0; }
  html, body { width: 1200px; height: 1097px; overflow: hidden; background: #fff; }
  body { font-family: "Lato", sans-serif; color: var(--ink); position: relative; }

  .hero { position: absolute; left: 0; top: 0; width: 1200px; height: 502px; overflow: hidden; }
  .hero-shapes { position: absolute; inset: 0; }
  .hero-rule { position: absolute; left: 0; top: 502px; width: 1200px; height: 3px; background: var(--orange); }
  .hero-rule-thin { position: absolute; left: 0; top: 507px; width: 1200px; height: 1px; background: var(--brown); }

  .brand { position: absolute; left: 99px; top: 52px; font-family: "Lato", sans-serif; font-weight: 700; font-size: 34px; line-height: 1; color: var(--ink); }

  .menu-toggle { position: absolute; left: 1065px; top: 36px; width: 36px; height: 29px; background: #000; display: flex; flex-direction: column; justify-content: center; align-items: center; gap: 3px; }
  .menu-toggle span { display: block; width: 20px; height: 2px; background: #fff; }

  .facts { position: absolute; left: 100px; top: 174px; width: 472px; list-style: none; }
  .facts li { position: relative; padding-left: 24px; font-size: 13px; line-height: 14px; color: #333; margin-bottom: 15px; }
  .facts li::before { content: ""; position: absolute; left: 0; top: 2px; width: 11px; height: 10px; background: var(--orange-deep); clip-path: polygon(50% 0, 100% 100%, 0 100%); }
  .facts li.down::before { transform: rotate(180deg); }
  .facts li.left::before { transform: rotate(-90deg); }

  .cta { position: absolute; left: 105px; top: 436px; width: 117px; height: 32px; background: #1a1a1a; color: #fff; font-size: 13px; display: flex; align-items: center; justify-content: center; text-decoration: none; box-shadow: 3px 3px 0 var(--orange); }

  .slider-dots { position: absolute; left: 1173px; top: 487px; display: flex; gap: 3px; }
  .slider-dots span { width: 6px; height: 6px; border-radius: 50%; background: #fff; }
  .slider-dots span.active { background: var(--orange); }

  .features { position: absolute; left: 100px; top: 606px; width: 1000px; display: flex; gap: 21px; }
  .feature { width: 319px; text-align: center; }
  .feature-photo { width: 319px; height: 203px; border: 3px solid var(--frame); }
  .feature-title { margin-top: 29px; min-height: 32px; font-family: "Ubuntu", sans-serif; font-weight: 700; font-size: 17px; line-height: 16px; color: #1a1a1a; text-transform: uppercase; }
  .feature-text { margin: 24px -3px 0; font-weight: 300; font-size: 14.5px; line-height: 19px; color: #222; }

  .site-footer { position: absolute; left: 0; top: 1027px; width: 1200px; height: 70px; background: var(--footer); color: #ddd; font-size: 11.5px; }
  .site-footer p { position: absolute; left: 0; width: 1192px; top: 28px; text-align: center; }
  .site-footer a { color: var(--orange); text-decoration: none; }
</style>
</head>
<body>
  <header class="hero">
    <svg class="hero-shapes" width="1200" height="502" viewBox="0 0 1200 502">
      <defs>
        <linearGradient id="heroPhotoTone" x1="0" y1="0" x2="1" y2="1">
          <stop offset="0" stop-color="#d9d6d3"/>
          <stop offset="0.45" stop-color="#b48a72"/>
          <stop offset="0.75" stop-color="#d87a3a"/>
          <stop offset="1" stop-color="#c9c4c0"/>
        </linearGradient>
      </defs>
      <rect width="1200" height="502" fill="var(--soft)"/>
      <polygon points="0,0 220,0 0,260" fill="#ffffff"/>
      <polygon points="0,322 107,502 0,502" fill="var(--orange-deep)"/>
      <polygon points="0,322 83,438 72,440 0,340" fill="var(--brown)"/>
      <polygon points="722,0 840,0 815,162 698,158" fill="var(--orange-deep)"/>
      <polygon points="752,128 802,128 784,224 738,216" fill="var(--brown)"/>
      <polygon points="798,338 818,338 770,502 728,502" fill="var(--orange-deep)"/>
      <polygon points="840,0 1200,0 1200,502 763,502" fill="url(#heroPhotoTone)" role="img" aria-label="Photo of a distressed woman reaching for an orange prescription pill bottle"/>
    </svg>

    <div class="brand">Veltrix</div>

    <div class="menu-toggle" aria-label="Menu"><span></span><span></span><span></span></div>

    <ul class="facts">
      <li>Nearly 2 million Americans abused or were dependant on prescription opioids in 2014</li>
      <li class="down">About 16 million people in the US abuse prescription medication</li>
      <li>Drug overdose is the leading cause of accidental death in the US, with 47,055 lethal drug overdoses in 2014</li>
      <li class="left">Each day, 78 people die from an overdose of prescription painkillers in the US.</li>
      <li class="left">Every day, over 2600 people are treated in emergency departments for misusing prescription opioids</li>
      <li>1 death every 19 mins</li>
      <li class="down">100,000,000 in chronic pain, How Many More Must Die?</li>
    </ul>

    <a class="cta" href="#">Sign Up Now</a>

    <div class="slider-dots"><span class="active"></span><span></span></div>
  </header>
  <div class="hero-rule"></div>
  <div class="hero-rule-thin"></div>

  <main class="features">
    <article class="feature">
      <div class="feature-photo" role="img" aria-label="Photo of officers and a coroner moving a stretcher by a brick wall" style="background: linear-gradient(135deg, #8a4a3a 0%, #6e5a4c 50%, #8fa45a 100%);"></div>
      <h2 class="feature-title">Veltrix Protects Doctor</h2>
      <p class="feature-text">Lets say Your Worst Case Scenario Happens… Your Patient Dies.....&nbsp; Now the Family Says..... "you got them addicted"</p>
    </article>
    <article class="feature">
      <div class="feature-photo" role="img" aria-label="Photo of a man in a suit seated at a courtroom table" style="background: linear-gradient(135deg, #d8cfb4 0%, #a8875e 55%, #3a3a40 100%);"></div>
      <h2 class="feature-title">What’s in Your Chart Right Now<br>That is Protecting You???</h2>
      <p class="feature-text">Lets say Your Worst Case Scenario Happens… Your Patient Dies.....&nbsp; Now the Family Says..... "you got them addicted"</p>
    </article>
    <article class="feature">
      <div class="feature-photo" role="img" aria-label="Photo of hands pouring pills beside a glass of whiskey and cigarettes" style="background: linear-gradient(135deg, #d9dde3 0%, #e6c9b8 45%, #9a5a2a 80%, #eeeeee 100%);"></div>
      <h2 class="feature-title">How Well Do You (Dr.) Know<br>Your Patient??</h2>
      <p class="feature-text">Veltrix was designed to give Patient's Individualized Opioid Education and Counseling and Provide a Risk Management Package to Physicians with Signatures of Understandings</p>
    </article>
  </main>

  <footer class="site-footer">
    <p>Copyrights © <a href="#">Yoursite</a>, All Rights Reserved</p>
  </footer>
</body>
</html>
```